Detail Shop Business card design

i need a business card design for my new detailing company called 'Brisk's Polish Works'. i want an all black and white design . simple, direct and to the point. i want the designer to choose a fitting font to match the logothe front should have logo, address, phone and email and the back side should have a slogan and text indicating that we offer services on anything including cars, trucks, motorcycles and RVs. slogan will read "we take pride in your ride"
maybe also very small on the back side the IG icon with Brisks_Polish_Works

phone 208.417.6352
address 3847 E Larkin Ave
Spokane WA 99214
email: BrisksPolish@mailvexo.com

Target Market(s)

all ages , auto enthusiasts

Industry/Entity Type

Automotive

Contact Information for Business Card

the front should have logo, address, phone and email and the back side should have a slogan and text indicating that we offer services on anything including cars, trucks, motorcycles and RVs. slogan will read "we take pride in your ride"

phone 208.417.6352
address 3847 E Larkin Ave
Spokane WA 99214

Colors
000000
ffffff

Requirements
Must have
• bold font and very simple design with good spacing
Nice to have
• anything creative from the designer indicating we service any types of vehicles
Should not have
• any colors ,

```html
<!DOCTYPE html>
<html lang="en">
<head>
<meta charset="UTF-8">
<title>Brisk's Polish Works – Business Card Back</title>
<link href="https://fonts.googleapis.com/css2?family=Bitter:wght@800&family=Lobster&display=swap" rel="stylesheet">
<style>
  :root {
    --paper: #ffffff;
    --ink: #000000;
    --emblem: #232323;
    --text: #ffffff;
  }
  html, body {
    margin: 0;
    padding: 0;
    width: 1200px;
    height: 1200px;
    overflow: hidden;
    background: var(--paper);
  }
  .canvas {
    position: relative;
    width: 1200px;
    height: 1200px;
    background: var(--paper);
  }
  .card-back {
    position: absolute;
    left: 0;
    top: 258px;
    width: 1200px;
    height: 684px;
    background: var(--ink);
    overflow: hidden;
  }
  .emblem-area {
    position: absolute;
    left: 80px;
    top: 0;
    width: 1000px;
    height: 684px;
    background: radial-gradient(ellipse 52% 70% at 55% 75%, var(--emblem) 0%, var(--emblem) 70%, rgba(35,35,35,0) 100%);
  }
  .services-heading,
  .service-item,
  .handle-name {
    position: absolute;
    margin: 0;
    font-family: "Bitter", Georgia, serif;
    font-weight: 800;
    color: var(--text);
    white-space: nowrap;
    line-height: 1;
  }
  .services-heading {
    left: 240px;
    top: 66px;
    font-size: 42px;
    letter-spacing: -0.5px;
  }
  .service-list {
    list-style: none;
    margin: 0;
    padding: 0;
  }
  .service-item {
    left: 296px;
    font-size: 40px;
  }
  .service-item .star {
    display: inline-block;
    width: 44px;
    font-size: 34px;
  }
  .service-item:nth-child(1) { top: 138px; }
  .service-item:nth-child(2) { top: 204px; }
  .service-item:nth-child(3) { top: 270px; }
  .service-item:nth-child(4) { top: 336px; }
  .slogan {
    position: absolute;
    left: 0;
    width: 1200px;
    top: 424px;
    margin: 0;
    text-align: center;
    font-family: "Lobster", "Brush Script MT", cursive;
    font-weight: 400;
    font-size: 58px;
    color: var(--text);
    transform: translateX(4px);
  }
  .social-handle {
    position: absolute;
    left: 309px;
    top: 554px;
    display: flex;
    align-items: center;
    gap: 34px;
  }
  .handle-mark {
    width: 52px;
    height: 52px;
    border: 6px solid var(--text);
    border-radius: 6px;
    box-sizing: border-box;
  }
  .handle-name {
    position: static;
    font-size: 44px;
  }
</style>
</head>
<body>
  <main class="canvas">
    <section class="card-back">
      <div class="emblem-area" role="img" aria-label="Faint dark-grey brand emblem with a hot rod behind the text"></div>
      <h2 class="services-heading">We service anything including:</h2>
      <ul class="service-list">
        <li class="service-item"><span class="star">★</span>Cars</li>
        <li class="service-item"><span class="star">★</span>Trucks</li>
        <li class="service-item"><span class="star">★</span>Motorcycles</li>
        <li class="service-item"><span class="star">★</span>RVs</li>
      </ul>
      <p class="slogan">"We Take Pride in Your Ride"</p>
      <div class="social-handle">
        <span class="handle-mark" aria-hidden="true"></span>
        <span class="handle-name">Brisks_Polish_Works</span>
      </div>
    </section>
  </main>
</body>
</html>
```